Zeltrova - Clever Automation

We are a software house for Audio Visual Systems integration/automation and home automation. we develop innovative software to automate a variety of devices mainly related to audio visuals and we design touch panel user interfaces to control these systems.

We would like to see designs that stick to our colours and theme, which you can find on our webpage www.zeltrova.com.au

The final design should communicate touch panels, innovation, software and automation.

Industry/Entity Type

Software

Requirements
Must have
• The business card must show the following information:
Name example : Derek Thalwin
Qualification example: B Eng ICT(CompSys) Dip EngPrac
Title example : Control Systems Programmer
Mobile Phone, Company phone, Email address ,Company website

```html
<!DOCTYPE html>
<html lang="en">
<head>
<meta charset="utf-8">
<title>Zeltrova – Business Card</title>
<link rel="stylesheet" href="https://fonts.googleapis.com/css2?family=Questrial&family=Mulish:wght@700&display=swap">
<style>
  :root {
    --brand-blue: #2a78c2;
    --brand-green: #1e9d57;
    --ink: #3d3d3d;
    --ink-soft: #555;
    --card: #ffffff;
    --backdrop: #2e2e2e;
    --rule: #9a9a9a;
  }
  * { margin: 0; padding: 0; box-sizing: border-box; }
  html, body { width: 1200px; height: 750px; overflow: hidden; }
  body {
    position: relative;
    background: var(--backdrop);
    font-family: "Questrial", "Century Gothic", sans-serif;
    color: var(--ink);
  }
  .card {
    position: absolute;
    width: 511px;
    height: 292px;
    background: var(--card);
    border-radius: 12px;
    overflow: hidden;
  }
  .card--front { left: 77px; top: 117px; }
  .card--back  { left: 613px; top: 324px; }

  .wordmark {
    position: absolute;
    display: flex;
    align-items: center;
    font-family: "Questrial", "Century Gothic", sans-serif;
    color: var(--brand-blue);
    letter-spacing: 0.5px;
    line-height: 1;
  }
  .wordmark__square {
    display: block;
    background: var(--brand-green);
    border-radius: 3px;
  }
  .card--front .wordmark { left: 20px; top: 20px; font-size: 30px; gap: 10px; }
  .card--front .wordmark__square { width: 32px; height: 32px; }
  .card--back .wordmark { left: 50%; top: 112px; transform: translateX(-50%); font-size: 40px; gap: 14px; }
  .card--back .wordmark__square { width: 44px; height: 44px; }

  .header-stripes {
    position: absolute;
    left: 228px;
    right: 0;
    top: 29px;
  }
  .header-stripes__green { height: 3px; background: var(--brand-green); }
  .header-stripes__blue  { height: 15px; margin-top: 4px; background: var(--brand-blue); }

  .person { position: absolute; left: 224px; top: 108px; }
  .person__name {
    font-family: "Mulish", "Century Gothic", sans-serif;
    font-weight: 700;
    font-size: 20px;
    color: var(--brand-blue);
    letter-spacing: -0.2px;
  }
  .person__title { font-size: 12px; color: var(--ink-soft); margin-top: 1px; }

  .address {
    position: absolute;
    right: 311px;
    top: 222px;
    text-align: right;
    font-size: 12px;
    line-height: 16px;
    color: var(--ink);
  }
  .divider {
    position: absolute;
    left: 210px;
    top: 178px;
    width: 1px;
    height: 86px;
    background: var(--rule);
  }
  .contacts { position: absolute; left: 225px; top: 189px; list-style: none; }
  .contacts li {
    display: flex;
    align-items: center;
    height: 16.5px;
    font-size: 12.5px;
    color: var(--ink);
  }
  .contacts svg { width: 12px; height: 12px; margin-right: 8px; flex: none; }

  .card--back .site {
    position: absolute;
    left: 0; right: 0;
    top: 266px;
    text-align: center;
    font-size: 13px;
    color: var(--ink);
  }
</style>
</head>
<body>

<section class="card card--front" aria-label="Business card front">
  <div class="wordmark"><span class="wordmark__square"></span><span>zeltrova</span></div>
  <div class="header-stripes">
    <div class="header-stripes__green"></div>
    <div class="header-stripes__blue"></div>
  </div>

  <div class="person">
    <p class="person__name">Derek Thalwin</p>
    <p class="person__title">Control Systems Programmer</p>
  </div>

  <address class="address" style="font-style:normal">
    14 Millbrook Lane<br>
    Penwick, NSW, 2749
  </address>

  <div class="divider"></div>

  <ul class="contacts">
    <li>
      <svg viewBox="0 0 12 12" aria-hidden="true"><circle cx="6" cy="6" r="6" fill="var(--brand-blue)"/><rect x="4" y="2.3" width="4" height="7.4" rx="0.8" fill="#fff"/><rect x="4.7" y="3.2" width="2.6" height="4.4" fill="var(--brand-blue)"/></svg>
      0412 585 903
    </li>
    <li>
      <svg viewBox="0 0 12 12" aria-hidden="true"><circle cx="6" cy="6" r="6" fill="var(--brand-blue)"/><path d="M3.4 3.2c.5-.5 1-.5 1.3 0l.6 1c.2.4 0 .7-.3 1-.2.2-.2.4 0 .7.4.6.8 1 1.3 1.3.3.2.5.2.7 0 .3-.3.6-.5 1-.3l1 .6c.5.3.5.8 0 1.3-.8.8-2 .7-3.3-.3-1-.8-1.8-1.6-2.5-2.6-.7-1.2-.6-2.1.2-2.7z" fill="#fff"/></svg>
      0245 318 772
    </li>
    <li>
      <svg viewBox="0 0 12 12" aria-hidden="true"><circle cx="6" cy="6" r="6" fill="var(--brand-blue)"/><rect x="2.6" y="3.6" width="6.8" height="4.8" rx="0.6" fill="#fff"/><path d="M2.8 3.9 6 6.3l3.2-2.4" fill="none" stroke="var(--brand-blue)" stroke-width="0.8"/></svg>
      dthalwin@zeltrova.com.au
    </li>
    <li>
      <svg viewBox="0 0 12 12" aria-hidden="true"><circle cx="6" cy="6" r="6" fill="var(--brand-blue)"/><circle cx="6" cy="6" r="3.6" fill="none" stroke="#fff" stroke-width="0.8"/><ellipse cx="6" cy="6" rx="1.5" ry="3.6" fill="none" stroke="#fff" stroke-width="0.7"/><path d="M2.4 6h7.2" stroke="#fff" stroke-width="0.7"/></svg>
      www.zeltrova.com.au
    </li>
  </ul>
</section>

<section class="card card--back" aria-label="Business card back">
  <div class="wordmark"><span class="wordmark__square"></span><span>zeltrova</span></div>
  <p class="site">www.zeltrova.com.au</p>
</section>

</body>
</html>
```